Bluecrest Learning Corps by graduating students from college in two years

Based on the logo design, create stationary and business cards for
Dr. Venrel T Oskamp, CEO, (703) 482-1736
and Marisa Deltoft, Respresentative, (301) 647-2208
Address: 4719 Pellham Court, Harlow Ridge, VA 22190
Incorporate elelments of the logo

Target Market(s)

USA

Font styles to use
Other font styles liked:
• match with the logo type style

```html
<!DOCTYPE html>
<html lang="en">
<head>
<meta charset="utf-8">
<title>Bluecrest Learning Corps — Stationery</title>
<link href="https://fonts.googleapis.com/css2?family=Libre+Baskerville:wght@400;700&family=Oswald:wght@400;600&family=Tinos:ital,wght@0,400;1,700&display=swap" rel="stylesheet">
<style>
  :root{
    --yellow:#F8C22E;
    --yellow-soft:#F9CF5A;
    --navy:#232A6B;
    --ink:#1d1d1d;
    --paper:#ffffff;
    --lavender:#E8E8F3;
    --board-top:#DDE2E4;
    --board-bottom:#C9CFD3;
  }
  *{margin:0;padding:0;box-sizing:border-box}
  html,body{width:1200px;height:916px;overflow:hidden}
  body{background:linear-gradient(180deg,var(--board-top),var(--board-bottom));position:relative;font-family:"Tinos",serif;color:var(--ink)}
  .icon-defs{position:absolute;width:0;height:0}

  .card{position:absolute;left:68px;width:438px;height:250px;background:var(--paper);overflow:hidden;box-shadow:0 8px 14px rgba(0,0,0,.28)}
  .card--front{top:65px;background:var(--yellow)}
  .card--ceo{top:339px}
  .card--rep{top:614px}

  .front-rings{position:absolute;inset:0;background:radial-gradient(ellipse at center,rgba(255,240,190,.45) 0%,rgba(230,170,40,.25) 60%,rgba(248,194,46,0) 75%)}
  .brand{position:absolute;display:flex;flex-direction:column;align-items:center;gap:6px;text-align:center}
  .brand__dot{border-radius:50%;background:var(--navy)}
  .brand__name{font-family:"Libre Baskerville",serif;font-weight:700;color:var(--navy);line-height:1.15}
  .card--front .brand{left:0;right:0;top:78px}
  .card--front .brand__dot{width:54px;height:54px;background:var(--paper)}
  .card--front .brand__name{font-size:15px}
  .card .brand--side{left:34px;top:60px;width:150px}
  .brand--side .brand__dot{width:38px;height:38px}
  .brand--side .brand__name{font-size:11.5px}

  .card__divider{position:absolute;left:219px;top:42px;width:1.5px;height:162px;background:var(--yellow)}
  .card__info{position:absolute;left:255px;top:62px;color:var(--navy);font-family:"Libre Baskerville",serif}
  .card__name{font-size:15.5px;font-weight:700;color:var(--yellow);line-height:1.1;white-space:nowrap}
  .card__role{font-family:"Tinos",serif;font-size:11.5px;margin-top:1px}
  .card__address{font-size:10px;line-height:15px;margin-top:9px;white-space:nowrap}
  .card__contacts{list-style:none;font-size:10px;line-height:15px;margin-top:8px}
  .card__contacts li{display:flex;align-items:center;gap:7px;white-space:nowrap}
  .card__wave{position:absolute;left:0;bottom:0;width:438px;height:250px}

  .icon{width:9px;height:9px;fill:var(--yellow);flex:none}

  .letterhead{position:absolute;left:563px;top:65px;width:558px;height:787px;background:var(--paper);overflow:hidden;box-shadow:0 8px 16px rgba(0,0,0,.28)}
  .lh__cap{position:absolute;inset:0}
  .lh__brand{position:absolute;left:29px;top:30px;width:110px;display:flex;flex-direction:column;align-items:center;gap:5px;text-align:center}
  .lh__brand .brand__dot{width:36px;height:36px}
  .lh__brand .brand__name{font-size:10.5px}
  .lh__contact{position:absolute;right:33px;top:37px;list-style:none;text-align:right;color:var(--navy);font-size:11.5px;line-height:15px}
  .lh__contact li{display:flex;justify-content:flex-end;align-items:center;gap:9px;white-space:nowrap}
  .lh__contact .icon{width:10px;height:10px}
  .lh__rule{position:absolute;top:118px;height:2px;background:var(--navy);left:29px;width:317px}
  .lh__rule--accent{left:346px;width:182px;height:3px;top:117px;background:var(--yellow)}
  .person{font-family:"Oswald",sans-serif;font-size:27px;line-height:1;color:var(--navy);white-space:nowrap}
  .person b{font-weight:600;color:var(--yellow)}
  .person-role{font-size:11px;margin-top:3px;padding-left:1px}
  .lh__sender{position:absolute;left:30px;top:159px}
  .lh__date{position:absolute;right:42px;top:167px;font-size:13px}
  .lh__direct{position:absolute;left:30px;top:217px;list-style:none;font-size:11px;line-height:13.2px;color:var(--navy)}
  .lh__direct li{display:flex;align-items:center;gap:6px}
  .lh__body{position:absolute;left:30px;top:277px;width:498px;font-size:12.1px;line-height:16px;text-align:justify}
  .lh__body p{margin-bottom:15px}
  .lh__signature{position:absolute;left:30px;top:556px;width:190px;height:58px;background:linear-gradient(90deg,rgba(80,80,95,.12),rgba(80,80,95,.04))}
  .lh__signer{position:absolute;left:30px;top:621px}

  .board-label{position:absolute;font-family:"Tinos",serif;font-style:italic;font-weight:700;font-size:33px;letter-spacing:1px;color:#f4f6f7;text-shadow:0 1px 2px rgba(0,0,0,.35)}
  .board-label--cards{left:143px;top:868px}
  .board-label--letter{left:728px;top:860px}
</style>
</head>
<body>

<svg class="icon-defs" aria-hidden="true">
  <defs>
    <symbol id="i-phone" viewBox="0 0 10 10"><path d="M2 .8 3.6 2.6 2.8 3.6Q4 6 6.4 7.2L7.4 6.4 9.2 8 8.2 9.4Q3.5 9 .6 1.8Z"/></symbol>
    <symbol id="i-web" viewBox="0 0 10 10"><circle cx="5" cy="5" r="4.3"/><path d="M.7 5h8.6M5 .7v8.6" stroke="#fff" stroke-width=".8"/></symbol>
    <symbol id="i-mail" viewBox="0 0 10 10"><rect x=".6" y="2" width="8.8" height="6.4" rx=".6"/><path d="M1 2.6 5 5.8 9 2.6" stroke="#fff" stroke-width=".8" fill="none"/></symbol>
    <symbol id="i-pin" viewBox="0 0 10 10"><path d="M5 .4A3.4 3.4 0 0 0 1.6 3.8C1.6 6.4 5 9.6 5 9.6S8.4 6.4 8.4 3.8A3.4 3.4 0 0 0 5 .4Z"/><circle cx="5" cy="3.8" r="1.3" fill="#fff"/></symbol>
  </defs>
</svg>

<section class="card card--front" aria-label="Business card front">
  <div class="front-rings" role="img" aria-label="Faint enlarged emblem rings on the yellow field"></div>
  <div class="brand">
    <span class="brand__dot"></span>
    <span class="brand__name">Bluecrest Learning Corps</span>
  </div>
</section>

<section class="card card--ceo" aria-label="Business card, CEO">
  <div class="brand brand--side">
    <span class="brand__dot"></span>
    <span class="brand__name">Bluecrest Learning Corps</span>
  </div>
  <div class="card__divider"></div>
  <div class="card__info">
    <div class="card__name">Dr. Venrel T Oskamp</div>
    <div class="card__role">CEO</div>
    <div class="card__address">4719 Pellham Court,<br>Harlow Ridge, VA 22190</div>
    <ul class="card__contacts">
      <li><svg class="icon"><use href="#i-phone"/></svg>(703) 482-1736</li>
      <li><svg class="icon"><use href="#i-web"/></svg>www.bluecrestcorps.org</li>
      <li><svg class="icon"><use href="#i-mail"/></svg>hello@bluecrestcorps.org</li>
    </ul>
  </div>
  <svg class="card__wave" viewBox="0 0 438 250" aria-hidden="true">
    <path d="M0 195Q200 238 438 234V250H0Z" fill="var(--yellow)"/>
    <path d="M147 219Q300 238 438 220V227Q300 242 147 220Z" fill="var(--navy)"/>
  </svg>
</section>

<section class="card card--rep" aria-label="Business card, representative">
  <div class="brand brand--side">
    <span class="brand__dot"></span>
    <span class="brand__name">Bluecrest Learning Corps</span>
  </div>
  <div class="card__divider"></div>
  <div class="card__info">
    <div class="card__name">Marisa Deltoft</div>
    <div class="card__role">Respresentative</div>
    <div class="card__address">4719 Pellham Court,<br>Harlow Ridge, VA 22190</div>
    <ul class="card__contacts">
      <li><svg class="icon"><use href="#i-phone"/></svg>(301) 647-2208</li>
      <li><svg class="icon"><use href="#i-web"/></svg>www.bluecrestcorps.org</li>
      <li><svg class="icon"><use href="#i-mail"/></svg>hello@bluecrestcorps.org</li>
    </ul>
  </div>
  <svg class="card__wave" viewBox="0 0 438 250" aria-hidden="true">
    <path d="M0 195Q200 238 438 234V250H0Z" fill="var(--yellow)"/>
    <path d="M147 219Q300 238 438 220V227Q300 242 147 220Z" fill="var(--navy)"/>
  </svg>
</section>

<article class="letterhead" aria-label="A4 letterhead">
  <svg class="lh__cap" viewBox="0 0 558 787" aria-hidden="true">
    <polygon points="181,588 558,533 558,787 261,787" fill="var(--lavender)" role="img" aria-label="Faint graduation cap illustration"/>
    <path d="M0 729Q250 772 558 775V787H0Z" fill="var(--yellow)"/>
    <path d="M190 754Q380 776 558 760V768Q380 784 190 755Z" fill="var(--navy)"/>
  </svg>

  <div class="lh__brand">
    <span class="brand__dot"></span>
    <span class="brand__name">Bluecrest Learning Corps</span>
  </div>
  <ul class="lh__contact">
    <li>(301) 647-2208<svg class="icon"><use href="#i-phone"/></svg></li>
    <li>www.bluecrestcorps.org<svg class="icon"><use href="#i-web"/></svg></li>
    <li>hello@bluecrestcorps.org<svg class="icon"><use href="#i-mail"/></svg></li>
    <li>4719 Pellham Court, Harlow Ridge, VA 22190<svg class="icon"><use href="#i-pin"/></svg></li>
  </ul>
  <div class="lh__rule"></div>
  <div class="lh__rule lh__rule--accent"></div>

  <div class="lh__sender">
    <div class="person"><b>Anneke</b> Voralis</div>
    <div class="person-role">Founder &amp; CEO</div>
  </div>
  <div class="lh__date">August-05-2019</div>
  <ul class="lh__direct">
    <li><svg class="icon"><use href="#i-phone"/></svg>(817) 536-2094</li>
    <li><svg class="icon"><use href="#i-web"/></svg>www.bluecrestcorps.org</li>
    <li><svg class="icon"><use href="#i-mail"/></svg>hello@bluecrestcorps.org</li>
  </ul>

  <div class="lh__body">
    <p>Lorem ipsum dolor sit amet, consectetuer adipiscing elit, sed diam nonummy nibh euismod tincidunt ut laoreet dolore magna aliquam erat volutpat. Ut wisi enim ad minim veniam, quis nostrud exerci tation ullamcorper suscipit lobortis</p>
    <p>Lorem ipsum dolor sit amet, cons ectetuer adipiscing elit, sed diam nonummy nibh euismod tincidunt ut laoreet dolore magna aliquam erat volutpat. Ut wisi enim ad minim veniam, quis nostrud exerci tation ullamcorper suscipit lobortis nisl ut aliquip ex ea commodo consequat. Lorem ipsum dolor sit amet, consectetuer olutpat. Ut wisi enim ad minim veniam, quis nostrud exerci tation ullamcorper suscipit lobortis nisl ut aliquip ex ea commodo consequat. Duis autem</p>
    <p>vel eum iriure dolor in hendrerit in vulputate velit esse molestie consequat, vel illum dolore eu feugiat nulla facilisis at vero eros et accumsan et iusto odio dignissim qui blandit praesent luptatum zzril delenit augue duis dolore te feugait nulla facilisi. Lorem ipsum dolor sit amet, cons ectetuer adipiscing elit, sed diam nonummy nibh euismod tincidunt ut laoreet dolore magna aliquam erat volutpat. Ut wisi enim .</p>
  </div>

  <div class="lh__signature" role="img" aria-label="Handwritten signature of the director"></div>
  <div class="lh__signer">
    <div class="person"><b>Tamsin</b> Korvelle</div>
    <div class="person-role">Director</div>
  </div>
</article>

<div class="board-label board-label--cards">Business card</div>
<div class="board-label board-label--letter">A4 Letterhead</div>

</body>
</html>
```